Dov's Personal Training -> also needs a logo

Services Frankston, Mornington, and Somerville

Specializes in in-home personal training

VaultPace style workouts

Not really preferential colors but needs to look modern and not stock photo

Industry/Entity Type

Training

Requirements
Must have
• 30% off first time customers on a package of 10

```html
<!DOCTYPE html>
<html lang="en">
<head>
<meta charset="utf-8">
<title>Dov's Personal Training</title>
<link rel="stylesheet" href="https://fonts.googleapis.com/css2?family=Archivo:wght@700;900&family=Jost:wght@400;600;700&display=swap">
<style>
  :root {
    --mint: #7fe5c7;
    --purple: #6a2bd9;
    --violet: #7a4ff0;
    --sky: #63b4f4;
    --teal: #74f6e0;
    --badge: #6fe5f2;
    --white: #ffffff;
    --bg-top: #f3f4f4;
    --bg-mid: #fbfbfb;
    --bg-bottom: #c9cbcb;
  }
  html, body {
    margin: 0;
    padding: 0;
    overflow: hidden;
  }
  .flyer {
    position: relative;
    width: 1200px;
    height: 900px;
    overflow: hidden;
    background: linear-gradient(180deg, var(--bg-top) 0%, var(--white) 40%, var(--bg-mid) 70%, #eceded 92%, var(--bg-bottom) 100%);
    font-family: "Jost", sans-serif;
  }
  .corner-bands {
    position: absolute;
    inset: 0;
  }
  .brand {
    position: absolute;
    left: 0;
    width: 1200px;
    top: 110px;
    text-align: center;
    color: var(--mint);
    font-family: "Jost", sans-serif;
    font-weight: 400;
  }
  .brand-mark {
    display: block;
    width: 190px;
    height: 190px;
    margin: 0 auto 40px;
    border-radius: 50%;
    background: var(--mint);
  }
  .brand-name {
    margin: 0;
    font-size: 84px;
    line-height: 1;
    letter-spacing: 0.32em;
    padding-left: 0.32em;
  }
  .brand-tagline {
    margin: 16px 0 0;
    font-size: 30px;
    line-height: 1;
    letter-spacing: 0.01em;
  }
  .specialties {
    position: absolute;
    left: 0;
    width: 1200px;
    top: 508px;
    text-align: center;
    color: var(--purple);
  }
  .specialties-title {
    margin: 0 0 8px;
    font-weight: 700;
    font-size: 34px;
    line-height: 1.1;
    letter-spacing: -0.01em;
  }
  .specialties-list {
    margin: 0;
    padding: 0;
    list-style: none;
    font-size: 31px;
    line-height: 1.3;
    font-weight: 400;
  }
  .offer {
    position: absolute;
    left: 58px;
    top: 590px;
    color: var(--violet);
    font-family: "Archivo", sans-serif;
  }
  .offer-amount {
    margin: 0;
    font-weight: 900;
    font-size: 116px;
    line-height: 0.84;
    letter-spacing: -0.02em;
  }
  .offer-terms {
    margin: 12px 0 0;
    font-weight: 700;
    font-size: 34px;
    line-height: 1.15;
    letter-spacing: -0.01em;
  }
  .service-area {
    position: absolute;
    left: 873px;
    top: 598px;
    width: 240px;
    height: 240px;
    border-radius: 50%;
    background: var(--badge);
    color: var(--white);
    text-align: center;
    display: flex;
    flex-direction: column;
    justify-content: center;
  }
  .service-area-title {
    margin: 0;
    font-weight: 700;
    font-size: 37px;
    line-height: 1;
  }
  .service-area-list {
    margin: 6px 0 0;
    padding: 0;
    list-style: none;
    font-size: 29px;
    line-height: 1.1;
    font-weight: 400;
  }
</style>
</head>
<body>
<main class="flyer">
  <svg class="corner-bands" width="1200" height="900" viewBox="0 0 1200 900" aria-hidden="true">
    <polygon points="700,900 1200,415 1200,545 830,900" fill="var(--teal)"/>
    <polygon points="830,900 1200,545 1200,680 965,900" fill="var(--violet)"/>
    <polygon points="965,900 1200,680 1200,900" fill="var(--sky)"/>
  </svg>

  <header class="brand">
    <span class="brand-mark" aria-hidden="true"></span>
    <h1 class="brand-name">DOV'S</h1>
    <p class="brand-tagline">PERSONAL TRAINING</p>
  </header>

  <section class="specialties">
    <h2 class="specialties-title">SPECIALIZES IN:</h2>
    <ul class="specialties-list">
      <li>in-home personal training</li>
      <li>VaultPace style workouts</li>
    </ul>
  </section>

  <section class="offer">
    <p class="offer-amount">30%<br>OFF</p>
    <p class="offer-terms">first time customers<br>on a package of 10</p>
  </section>

  <section class="service-area">
    <h2 class="service-area-title">SERVICES:</h2>
    <ul class="service-area-list">
      <li>FRANKSTON</li>
      <li>MORNINGTON</li>
      <li>SOMERVILLE</li>
    </ul>
  </section>
</main>
</body>
</html>
```